Business cards for veterinary clinic

Hi, We are looking for business cards to be designed for our other veterinary clinic. We were very happy with the design done for our other clinic a few months ago. We already have a logo for use which I will attach (please use the image not the text around.
We need a couple of different cards (same design with different names on them) produced

Industry/Entity Type

Veterinary

Contact Information for Business Card

Bellwood Creek Vet Clinic
47 Orchard Rd
Kangaroo Flat
VIC 3555
03) 5182 6390
clinic@bellwoodcreekvetclinic.com.au

Font styles to use
Sans Serif

Colors
0455a3
0592cd

Requirements
Must have
• Three different names
• 1. Generic (no name) with email clinic@bellwoodcreekvetclinic.com.au
• 2. Hollis Varne -Director with email hollis@bellwoodcreekvetclinic.com.au
• 3. Dorian Pike - Vet Director with email hollis@bellwoodcreekvetclinic.com.au

```html
<!DOCTYPE html>
<html lang="en">
<head>
<meta charset="utf-8">
<title>Bellwood Creek Vet Clinic – Business Card</title>
<link rel="stylesheet" href="https://fonts.googleapis.com/css2?family=Jost:wght@400;500&display=swap">
<style>
  :root {
    --stage: #1c2530;
    --card-blue: #1f4496;
    --card-blue-deep: #17377f;
    --brand-cyan: #62d2e2;
    --accent-blue: #0592cd;
    --ink-light: #f2f3ee;
    --rule: #e8ecef;
    --disc: #e9f6f8;
  }
  * { box-sizing: border-box; margin: 0; padding: 0; }
  html, body { width: 1200px; height: 1000px; overflow: hidden; }
  body {
    background: var(--stage);
    font-family: "Jost", sans-serif;
    position: relative;
  }
  .card {
    position: absolute;
    top: 130px;
    width: 420px;
    height: 740px;
    border-radius: 6px;
    background: linear-gradient(160deg, var(--card-blue) 0%, var(--card-blue-deep) 100%);
    overflow: hidden;
  }
  .card--front { left: 150px; }
  .card--back { left: 630px; }

  .front__mark {
    width: 170px; height: 170px;
    margin: 46px auto 0;
    border-radius: 50%;
    background: var(--disc);
  }
  .front__clinic {
    margin-top: 22px;
    text-align: center;
    color: var(--brand-cyan);
    font-size: 40px;
    font-weight: 400;
    line-height: 1.05;
    letter-spacing: 1px;
    text-transform: uppercase;
  }
  .rule {
    height: 2px;
    background: var(--rule);
    margin: 24px 34px;
  }
  .front__person { text-align: center; }
  .front__name {
    color: var(--ink-light);
    font-size: 40px;
    font-weight: 500;
    letter-spacing: 1px;
    line-height: 1;
  }
  .front__role {
    color: var(--brand-cyan);
    font-size: 18px;
    letter-spacing: 1px;
    margin-top: 2px;
  }
  .front__phone {
    text-align: center;
    color: var(--ink-light);
    font-size: 64px;
    font-weight: 400;
    letter-spacing: 2px;
    line-height: 1;
  }
  .front__details {
    font-style: normal;
    text-align: center;
    color: var(--ink-light);
    font-size: 15px;
    letter-spacing: 1px;
    line-height: 1.45;
    text-transform: uppercase;
  }

  .back__disc {
    position: absolute;
    left: -90px;
    top: 380px;
    width: 600px;
    height: 600px;
  }
  .back__name {
    position: absolute;
    top: 520px; left: 0; right: 0;
    text-align: center;
    color: var(--accent-blue);
    font-size: 40px;
    font-weight: 400;
    line-height: 1.05;
    letter-spacing: 1px;
    text-transform: uppercase;
  }
</style>
</head>
<body>
  <section class="card card--front" aria-label="Business card front">
    <div class="front__mark" aria-hidden="true"></div>
    <h1 class="front__clinic">Bellwood Creek<br>Vet Clinic</h1>
    <div class="rule"></div>
    <div class="front__person">
      <p class="front__name">HOLLIS VARNE</p>
      <p class="front__role">DIRECTOR</p>
    </div>
    <div class="rule"></div>
    <p class="front__phone">5182 6390</p>
    <div class="rule"></div>
    <address class="front__details">
      47 Orchard Rd Millbrook<br>
      Vale VIC 3871 03<br>
      hollis@bellwoodcreekvetclinic.com.au
    </address>
    <div class="rule"></div>
  </section>

  <section class="card card--back" aria-label="Business card back">
    <svg class="back__disc" viewBox="0 0 600 600" aria-hidden="true">
      <circle cx="300" cy="300" r="296" fill="var(--disc)" stroke="var(--accent-blue)" stroke-width="8"/>
    </svg>
    <p class="back__name">Bellwood Creek<br>Vet Clinic</p>
  </section>
</body>
</html>
```